Internationally renowned speaker/campaigner needs a book cover

I need a preliminary cover design for my new book "HALF-LANTERN".

I'm a medical doctor and an internationally renowned speaker and campaigner for human-centered and compassionate healthcare, co-founder of an international social movement PETALS in MEDICINE (http://petalsinmedicine-example.com), and successful author of the book 'ROOM TO LISTEN - Ways to cherish your clients and your work' (http://www.shopvantra-example.com/ROOM-LISTEN-cherish-your-clients/dp/9082614530)

The subtitle of HALF-LANTERN is: "How our one-eyed materialistic science leads to inequality, greed, poverty, violence, ill-health and environmental destruction (and what we can do about it)"

Author: Dr GARETH PELLWICK

Preliminary book blurb:
"As social activists and environmental campaigners we are continuously sabotaging our cause because our strategies are unconsciously supporting the materialistic foundations of our broken world.

Our materialistic science sees the natural world and even people as innate objects, without consciousness or connection. Modern medicine treats patients as broken machines to be fixed, not as conscious, subjective beings. And economic theory says every person is an independent agent, striving to maximize advantage. We turn every human and natural gift into a commodity to be owned, controlled, bought and sold.

Our social policies, education system, justice system and even our democracy assume that incentives, rewards and punishments are the ‘real’ motives for human behavior. Our purpose in life is to ‘get ahead’ and accumulate material goods. Therein lies competition, insecurity, greed, violence, ill-health and the destruction of the natural environment.

Materialistic science is simply blind to the life-world of consciousness, intelligence, purpose and deep interdependence in all natural and human systems. We all know that compassion, kindness, love, and human creativity are the real foundation of our communities, not mindless competition.

But so immersed are we in materialistic assumptions, that in our campaigns we mistakenly adopt tools and strategies from the existing system in our struggle for a better world. But the moment we fight against anything, or demonize our opposition, or sell our ideas for money, or charitably impose our solutions, we only strengthen the material world.

Instead, we have to be the change we want to see: grow an economy of generosity and gifting, freely share ideas, focus on solutions not problems, and deeply believe in the capacity for creativity and healing in every person and every community. You can download this book for free at halflantern-example.org."

Design brief
I need a compelling front page image and title design that conveys the idea that our science is one-eyed or half-blind, hence the title name 'half-lantern', which means half-science.

Our predominant science only sees the material world, not the conscious world. We need both.

I'm also preparing a QUORx talk on the subject and want the compelling image and title to use for this purpose also.

The genre of books is in the class of leadership, entrepreneurs, positive psychology, community development - and I have uploaded some cover images of books in this class. The cover of my current book, ROOM TO LISTEN, has elements of the style I'm looking for: bold, bright, simple, metaphorical, a surprising juxtaposition of technical and human.

The way I develop and market the book will be congruent with the ideas expressed. I will give the e-book away for free and invite people to make a donation if they like it (gift economy). The book will be published on the website unfinished, inviting comments, suggestions, stories and ideas to be included in the finished book. So to a degree, the content of the book will be fully developed by crowdsourcing living examples of the core ideas and creating a community of conversation (including a Chatterbay page). I'll later be looking for a simple WordPress website design based on the book cover graphic, fonts and colours.

So this first design brief and contract is for an e-book cover and later the book will be self-published as a paperback using PressNook.

Target Market(s)

The target audience is readers who are community leaders and social activists - all those utterly passionate about creating a better world, whether it's in the environment, education, healthcare, violence prevention, justice, health communities, etc.

Requirements
Must have
• A compelling image that symbolises the key idea - eyecatching
Should not have
• Must not express 'corporate' concepts, power or hierarchy

```html
<!DOCTYPE html>
<html lang="en">
<head>
<meta charset="utf-8">
<title>HALF-LANTERN — Dr Gareth Pellwick</title>
<link rel="stylesheet" href="https://fonts.googleapis.com/css2?family=League+Gothic&family=Oswald:wght@500;600&family=Merriweather:ital@1&display=swap">
<style>
  :root {
    --paper: #f8f8f6;
    --ink: #2a2b2e;
    --title-grey: #3e4045;
    --accent-red: #e8232b;
    --lens-light: #f1f2f2;
    --lens-mid: #e2e4e5;
  }
  html, body {
    margin: 0;
    padding: 0;
    width: 800px;
    height: 1200px;
    overflow: hidden;
    background: var(--paper);
  }
  .book-cover {
    position: relative;
    width: 800px;
    height: 1200px;
    background: var(--paper);
    overflow: hidden;
  }
  .cover-image {
    position: absolute;
    left: 50px;
    top: 70px;
    width: 700px;
    height: 380px;
    border-radius: 40px;
    background: radial-gradient(ellipse at 50% 45%, var(--lens-light) 0%, var(--lens-mid) 55%, var(--paper) 100%);
  }
  .cover-title {
    position: absolute;
    left: 0;
    top: 463px;
    width: 800px;
    margin: 0;
    text-align: center;
    white-space: nowrap;
    font-family: "League Gothic", "Oswald", sans-serif;
    font-weight: 400;
    font-size: 180px;
    line-height: 1;
    letter-spacing: 2px;
    color: var(--title-grey);
  }
  .cover-subtitle {
    position: absolute;
    left: 0;
    top: 709px;
    width: 800px;
    margin: 0;
    text-align: center;
    font-family: "Oswald", sans-serif;
    font-weight: 600;
    text-transform: uppercase;
    color: var(--ink);
  }
  .cover-subtitle .line {
    display: block;
    white-space: nowrap;
    font-size: 29px;
    line-height: 37px;
    letter-spacing: 0;
  }
  .cover-subtitle .highlight {
    color: var(--accent-red);
  }
  .cover-subtitle .aside {
    display: block;
    margin-top: 6px;
    font-family: "Merriweather", serif;
    font-style: italic;
    font-weight: 400;
    text-transform: none;
    font-size: 19px;
    line-height: 28px;
    color: var(--ink);
  }
  .cover-author {
    position: absolute;
    left: 0;
    top: 1055px;
    width: 800px;
    margin: 0;
    text-align: center;
    white-space: nowrap;
    font-family: "Oswald", sans-serif;
    font-weight: 600;
    text-transform: uppercase;
    color: var(--title-grey);
    font-size: 50px;
    line-height: 1;
    letter-spacing: 0.5px;
  }
  .cover-author .honorific {
    font-size: 36px;
    margin-right: 8px;
  }
</style>
</head>
<body>
  <main class="book-cover">
    <div class="cover-image" role="img" aria-label="Photograph of a pair of thick round black-rimmed spectacles with clear lenses, resting on a white surface with a soft reflection"></div>

    <h1 class="cover-title">HALF-LANTERN</h1>

    <p class="cover-subtitle">
      <span class="line">How our one-eyed materialistic science leads to</span>
      <span class="line highlight">Inequality, greed, poverty, violence, ill-health</span>
      <span class="line">and <span class="highlight">environmental destruction</span></span>
      <span class="aside">(and what we can do about it)</span>
    </p>

    <p class="cover-author"><span class="honorific">Dr</span>Gareth Pellwick</p>
  </main>
</body>
</html>
```